Electrictrian Contractor Website Design

We are working with an electrical contractor in California called Fennick Electric.

Some sites to use for content/competitors and inspiration:
https://corvanelectric.example
https://tralvenpage.example/web/contractor/ (lots of contractor website designs we've approved and continue to show clients)

Thank you for taking the time to consider designing a website for us. We are web developers based in Stockton, CA, USA. Most of our projects go through the same process. Understanding this process may help you win a project with us. We custom-code all of our websites in-house. We don’t have any requirements as to what tools you use for your design, but we prefer Figma files. For any design that we label as four-stars, we send it to the client for review. The client picks the final design they want us to use. Once we complete this process, we will continue to show additional clients all the four-star sites and purchase them later. Your designs will have multiple chances to sell. For better chances of success, we ask that you follow these guidelines.

IMAGES:
If you use any images or icons in the design, we ask that you have a link to the asset so we can purchase the image/icon. Most of the designs we submit do not have the customer’s images on them unless they have some great images. Be creative; show us the feeling you are trying to portray with your image choices. Use any royalty-free site you choose. We subscribe to Quorvane and mainly use their images, but we can purchase images outside of Quorvane.

PLEASE NOTE: we will not submit designs to clients with watermarks on the images.

FONTS:
We ask that you identify the fonts used in the design. This can be done in a message if you want. We typically use Pellmarsh Type and Quorvane Type.

CONTENT:
We're always open to different content and ideas. We often submit designs with stock images so the client can see our vision. We typically take pictures after the website launch to use their images with our vision. Lorem Ipsum is fine for paragraphs, but we ask that you write the headers in correct English. We want to be able to show the vision and identify the sections of the website.

INSPIRATION:
We typically add a couple of links in the brief of websites we like to help you get started in your design.

REVISIONS:
We do not often ask for revisions of the designs unless we see something in the design that may not appeal to the client. If there are slight changes that we want to make, we do that in the development process.

FEEDBACK:
We rarely give feedback on designs during the design process. We are working on many website projects and do not have the time to provide feedback. We usually respond if your request is well thought out and asks specific questions, but a note asking “feedback, please” usually goes unanswered

```html
<!DOCTYPE html>
<html lang="en">
<head>
<meta charset="utf-8">
<title>Fennick Electric — Electrical Contractor</title>
<link rel="stylesheet" href="https://fonts.googleapis.com/css2?family=Lato:wght@400;700;900&family=Montserrat:wght@600;700&display=swap">
<style>
:root{
  --blue:#0c3f8c;
  --blue-dark:#082e68;
  --yellow:#f6b800;
  --orange:#f08d00;
  --ink:#1c1c1c;
  --muted:#555b66;
  --line:#c9ccd2;
  --paper:#ffffff;
  --grey:#eef0f3;
}
*{box-sizing:border-box;margin:0;padding:0}
html,body{width:1200px;height:4563px;overflow:hidden;background:var(--paper)}
body{font-family:"Lato",Arial,sans-serif;color:var(--ink)}
.page{position:relative;width:1200px;height:4563px;overflow:hidden}
.abs{position:absolute}
.photo{position:absolute}
.heading{font-size:42px;font-weight:400;color:var(--ink);white-space:nowrap;display:flex;align-items:center;gap:10px}
.heading b{color:var(--blue);font-weight:700}
.dot-badge{display:inline-block;width:30px;height:30px;border-radius:50%;border:3px solid var(--yellow)}
.pill{position:absolute;height:36px;border-radius:18px;background:var(--blue);color:#fff;font-size:13px;display:flex;align-items:center;justify-content:space-between;padding:0 4px 0 14px}
.pill i{display:block;width:28px;height:28px;border-radius:50%;background:var(--yellow);border:2px solid #fff}

/* top bar */
.topbar{position:absolute;left:0;top:0;width:1200px;height:50px;background:var(--blue);color:#fff;font-size:13px;font-weight:700}
.topbar .item{position:absolute;top:15px;display:flex;align-items:center;gap:10px}
.topbar .ico{width:22px;height:22px;border:1.5px solid #fff;border-radius:50%}
.topbar .cta{position:absolute;left:940px;top:0;width:145px;height:50px;background:var(--yellow);color:var(--blue-dark);display:flex;align-items:center;justify-content:center}
.navbar{position:absolute;top:50px;left:0;width:1200px;height:66px;background:#fff}
.brand{position:absolute;color:var(--blue);font-weight:700;letter-spacing:5px;line-height:1}
.brand .l1{font-size:22px;display:block;padding-left:18px}
.brand .l2{font-size:22px;display:block;font-weight:700}
.menu{position:absolute;left:336px;top:27px;display:flex;gap:20px;font-size:13px;color:var(--ink)}
.menu .active{color:var(--blue);font-weight:700;position:relative}
.menu .active::before{content:"";position:absolute;left:9px;top:-14px;width:8px;height:8px;border-radius:50%;background:var(--yellow)}

/* hero */
.hero-text h2{font-size:30px;font-weight:400;color:var(--ink)}
.hero-text h1{font-family:"Montserrat",sans-serif;font-size:58px;font-weight:700;color:var(--blue);line-height:1.1;white-space:nowrap}
.hero-text h1 span{color:var(--yellow)}
.hero-text p{font-size:13px;line-height:29px;color:#2a2a2a;width:440px;margin-top:14px}

/* about */
.about p{font-size:13px;line-height:26px;color:var(--muted);width:445px;margin-bottom:10px}

/* facts */
.facts-title{font-size:40px;color:#fff;line-height:53px;font-weight:700}
.stat{position:absolute;top:1276px;font-family:"Montserrat",sans-serif;color:#fff;font-size:21px;line-height:30px;font-weight:600}
.stat em{font-style:normal;color:var(--yellow);display:block}
.vline{position:absolute;top:1267px;width:2px;height:106px;background:#fff}

/* services */
.card{position:absolute;background:#fff;box-shadow:0 2px 10px rgba(0,0,0,.18);text-align:center}
.card .img{position:absolute;left:12px;top:12px;right:12px}
.card .ic{position:absolute;width:52px;height:52px;border-radius:50%;background:#fff;display:flex;align-items:center;justify-content:center}
.card h3{position:absolute;left:0;right:0;font-size:21px;font-weight:700;color:var(--blue)}
.card p{position:absolute;left:40px;right:40px;font-size:12.5px;line-height:26px;color:#333}
.card .arrow{position:absolute;left:50%;margin-left:-9px}

/* news */
.news-date{font-size:13px;color:#888;letter-spacing:1px}
.news-title{font-size:16px;font-weight:700;border-left:3px solid var(--yellow);padding-left:12px;color:var(--ink)}
.news-text{font-size:12px;line-height:19px;color:#444}
.read{font-size:9px;color:var(--blue)}

/* testimonial */
.testi p{font-size:14px;line-height:27.5px;color:#fff;width:350px}

/* form */
.field label{display:block;font-size:15px;font-weight:700;color:var(--ink)}
.field span{display:block;font-size:13px;color:#888;margin-top:15px;padding-bottom:6px;border-bottom:1px solid #999}

/* footer */
.footer h4{font-size:16px;font-weight:700;color:#fff}
.footer ul{list-style:none;font-size:13px;color:#fff}
.flinks li{height:25px}
.social li{height:41px;display:flex;align-items:flex-start;gap:14px}
.social i{display:block;width:18px;height:18px;border-radius:50%;border:1.5px solid #fff}
.contact li{display:flex;gap:18px;align-items:flex-start;height:47px}
</style>
</head>
<body>
<div class="page">

<!-- top bar -->
<div class="topbar">
  <div class="item" style="left:110px"><span class="ico"></span>+1 555 014 2290</div>
  <div class="item" style="left:313px"><span class="ico"></span>hello@fennickelectric.example</div>
  <div class="cta">Free Consultation</div>
</div>

<div class="navbar">
  <div class="brand" style="left:110px;top:12px"><span class="l1">FENNICK</span><span class="l2">ELECTRIC</span></div>
  <nav class="menu">
    <span class="active">Home</span><span>About Us</span><span>Services</span><span>Projects</span><span>Careers</span><span>Testimonials</span><span>Blog</span>
  </nav>
  <div class="pill" style="left:959px;top:17px;width:126px">Contact Us <i></i></div>
</div>

<!-- hero -->
<div class="abs" style="left:0;top:116px;width:1200px;height:600px;background:linear-gradient(90deg,#f4f5f7,#e7e9ec)"></div>
<div class="photo" role="img" aria-label="Smiling electrician in hard hat and safety vest wiring an electrical panel" style="left:550px;top:116px;width:650px;height:600px;background:linear-gradient(120deg,#cfd3d8 0%,#9ea5ad 30%,#6b6f70 50%,#c9cf4a 75%,#e7e8ea 100%)"></div>
<svg class="abs" style="left:0;top:0" width="1200" height="760" viewBox="0 0 1200 760">
  <path d="M0,565 Q600,760 1200,565 L1200,760 L0,760 Z" fill="var(--yellow)"/>
  <path d="M0,590 Q600,845 1200,590 L1200,760 L0,760 Z" fill="#fff"/>
  <circle cx="582" cy="630" r="5" fill="var(--blue)"/>
  <circle cx="600" cy="630" r="5" fill="var(--yellow)"/>
  <circle cx="618" cy="630" r="5" fill="var(--blue)"/>
  <circle cx="600" cy="702" r="26" fill="#fff"/>
  <circle cx="600" cy="702" r="21" fill="var(--yellow)"/>
</svg>
<div class="abs hero-text" style="left:110px;top:202px">
  <h2>Welcome To</h2>
  <h1><span>Fennick</span> Electric</h1>
  <p>Duis aute irure dolor in reprehenderit in voluptate velit esse cillum dolore eu fugiat nulla pariatur. Excepteur sint occaecat cupidatat non proident, sunt in culpa qui officia deserunt mollit anim id est laborum.</p>
</div>
<div class="pill" style="left:112px;top:450px;width:128px">Get Started <i></i></div>

<!-- about -->
<svg class="abs" style="left:126px;top:738px" width="376" height="376" viewBox="0 0 376 376">
  <circle cx="188" cy="188" r="183" fill="none" stroke="var(--yellow)" stroke-width="7"/>
</svg>
<div class="photo" role="img" aria-label="Electrician's hands working inside a breaker panel" style="left:142px;top:754px;width:344px;height:344px;border-radius:50%;background:radial-gradient(circle at 45% 45%,#9aa3ad,#3e4650 70%,#23292f)"></div>
<div class="abs about" style="left:643px;top:762px">
  <div class="heading">About <b>Us</b> <span class="dot-badge"></span></div>
  <div style="height:30px"></div>
  <p>Sed ut perspiciatis unde omnis iste natus error sit voluptatem accusantium doloremque laudantium, totam rem aperiam, eaque ipsa quae ab illo inventore veritatis et quasi architecto beatae vitae dicta sunt explicabo.</p>
  <p>Nemo enim ipsam voluptatem quia voluptas sit aspernatur aut odit aut fugit, sed quia consequuntur magni dolores eos qui ratione voluptatem sequi nesciunt.</p>
</div>
<div class="pill" style="left:643px;top:1045px;width:128px">Read More <i></i></div>

<!-- facts -->
<svg class="abs" style="left:0;top:1080px" width="1200" height="410" viewBox="0 1080 1200 410">
  <defs>
    <linearGradient id="factsFill" x1="0" y1="0" x2="1" y2="0">
      <stop offset="0" stop-color="#1e58a8"/><stop offset=".5" stop-color="#0c3f8c"/><stop offset="1" stop-color="#1f5aaa"/>
    </linearGradient>
  </defs>
  <path d="M0,1095 Q600,1285 1200,1095 L1200,1480 Q600,1370 0,1480 Z" fill="url(#factsFill)" role="img" aria-label="Blue band over bundled electrical cables"/>
</svg>
<div class="abs facts-title" style="left:110px;top:1228px">Some<br>Important<br>Facts</div>
<div class="stat" style="left:440px"><em>5000+</em>Residential<br>Projects</div>
<div class="vline" style="left:620px"></div>
<div class="stat" style="left:675px"><em>1500+</em>Commercial<br>Projects</div>
<div class="vline" style="left:861px"></div>
<div class="stat" style="left:934px;top:1270px"><em>1000+</em>Industrial<br>Projects</div>

<!-- services -->
<div class="abs heading" style="left:452px;top:1545px">Our <b>Services</b> <span class="dot-badge"></span></div>

<div class="card" style="left:83px;top:1621px;width:335px;height:417px;border-bottom:5px solid var(--blue)">
  <div class="img photo" role="img" aria-label="Electrician in hard hat inspecting an industrial switchboard" style="height:197px;background:linear-gradient(110deg,#c8ccd1,#7a8088 55%,#d7d95a 80%,#9ca2a8)"></div>
  <div class="ic" style="left:30px;top:192px"><svg width="30" height="26" viewBox="0 0 30 26"><rect x="2" y="6" width="12" height="19" fill="none" stroke="var(--blue)" stroke-width="2"/><rect x="14" y="1" width="13" height="24" fill="none" stroke="var(--blue)" stroke-width="2"/></svg></div>
  <h3 style="top:218px">Industrial Service</h3>
  <p style="top:252px">Lorem ipsum dolor sit amet, consectetur adipiscing elit, sed do eiusmod tempor incididunt ut labore et dolore magna aliqua.</p>
  <svg class="arrow" style="top:360px" width="18" height="12" viewBox="0 0 18 12"><path d="M1,6 H16 M11,1 L16,6 L11,11" fill="none" stroke="var(--ink)" stroke-width="1.5"/></svg>
</div>

<div class="card" style="left:429px;top:1673px;width:335px;height:418px;background:var(--blue);border-bottom:5px solid var(--yellow)">
  <div class="img photo" role="img" aria-label="Electrician fitting a ceiling light in a bright home interior" style="height:212px;left:0;right:0;top:0;background:linear-gradient(100deg,#ece9e4,#d5d0c8 55%,#7b7f86 80%,#e8e4de)"></div>
  <div class="ic" style="left:22px;top:184px"><svg width="30" height="26" viewBox="0 0 30 26"><path d="M3,12 L15,2 L27,12 M6,10 V24 H24 V10" fill="none" stroke="var(--blue)" stroke-width="2"/><rect x="12" y="15" width="6" height="9" fill="none" stroke="var(--blue)" stroke-width="2"/></svg></div>
  <h3 style="top:243px;color:#fff">Residential Service</h3>
  <p style="top:276px;color:#fff;left:44px;right:44px;line-height:23px">Lorem ipsum dolor sit amet, consectetur adipiscing elit, sed do eiusmod tempor incididunt ut labore et dolore magna aliqua.</p>
  <svg class="arrow" style="top:378px" width="18" height="12" viewBox="0 0 18 12"><path d="M1,6 H16 M11,1 L16,6 L11,11" fill="none" stroke="#fff" stroke-width="1.5"/></svg>
</div>

<div class="card" style="left:775px;top:1621px;width:335px;height:417px;border-bottom:5px solid var(--blue)">
  <div class="img photo" role="img" aria-label="Technician wiring a commercial data and power cabinet" style="height:197px;background:linear-gradient(110deg,#8aa7c8,#3f5f8a 45%,#c6b79f 70%,#2f4a72)"></div>
  <div class="ic" style="left:30px;top:192px"><svg width="30" height="26" viewBox="0 0 30 26"><rect x="3" y="4" width="10" height="21" fill="none" stroke="var(--blue)" stroke-width="2"/><rect x="13" y="9" width="14" height="16" fill="none" stroke="var(--blue)" stroke-width="2"/></svg></div>
  <h3 style="top:218px">Commercial Service</h3>
  <p style="top:252px">Lorem ipsum dolor sit amet, consectetur adipiscing elit, sed do eiusmod tempor incididunt ut labore et dolore magna aliqua.</p>
  <svg class="arrow" style="top:362px" width="18" height="12" viewBox="0 0 18 12"><path d="M1,6 H16 M11,1 L16,6 L11,11" fill="none" stroke="var(--ink)" stroke-width="1.5"/></svg>
</div>

<!-- partners -->
<svg class="abs" style="left:0;top:2110px" width="1200" height="520" viewBox="0 2110 1200 520">
  <defs>
    <linearGradient id="orangeFill" x1="0" y1="0" x2="1" y2="1">
      <stop offset="0" stop-color="#f7bc00"/><stop offset=".55" stop-color="#f39a00"/><stop offset="1" stop-color="#f08300"/>
    </linearGradient>
  </defs>
  <path d="M0,2118 Q600,2330 1200,2118 L1200,2510 Q600,2720 0,2510 Z" fill="url(#orangeFill)" role="img" aria-label="Warm orange sky with power transmission tower"/>
  <path d="M16,2325 H30 M21,2320 L16,2325 L21,2330" fill="none" stroke="#fff" stroke-width="1.5"/>
  <path d="M1146,2325 H1160 M1155,2320 L1160,2325 L1155,2330" fill="none" stroke="#fff" stroke-width="1.5"/>
  <rect x="115" y="2392" width="168" height="72" rx="4" fill="none" stroke="#fff" stroke-width="3"/>
  <circle cx="370" cy="2427" r="34" fill="rgba(255,255,255,.85)"/>
  <rect x="526" y="2404" width="138" height="46" rx="23" fill="rgba(255,255,255,.85)"/>
  <ellipse cx="806" cy="2428" rx="62" ry="32" fill="rgba(255,255,255,.85)"/>
  <rect x="962" y="2398" width="120" height="44" rx="4" fill="rgba(255,255,255,.85)"/>
</svg>
<div class="abs heading" style="left:452px;top:2292px;color:#fff">Our <b style="color:var(--blue)">Partners</b> <span class="dot-badge" style="border-color:#fff"></span></div>
<div class="pill" style="left:538px;top:2490px;width:118px">View All <i></i></div>
<div class="pill" style="left:540px;top:2128px;width:118px">View All <i></i></div>

<!-- news -->
<div class="abs heading" style="left:108px;top:2678px">News &amp; <b>Update</b> <span class="dot-badge"></span></div>
<div class="abs" style="left:110px;top:2756px;width:292px">
  <div class="news-date">07.9.24</div>
  <div class="news-title" style="margin-top:14px">Lorem ipsum dolor sit amet</div>
  <div class="news-text" style="margin-top:12px">Ut enim ad minim veniam quis nostrud exercitation ullamco laboris.</div>
  <div style="border-top:1px solid var(--line);margin-top:22px;width:292px"></div>
  <div class="news-date" style="margin-top:20px">24.3.24</div>
  <div class="news-title" style="margin-top:14px">Lorem ipsum dolor sit amet</div>
  <div class="news-text" style="margin-top:12px">Ut enim ad minim veniam quis nostrud exercitation ullamco laboris.</div>
</div>

<div class="photo" role="img" aria-label="Two engineers in hard hats at an electrical substation" style="left:480px;top:2685px;width:291px;height:190px;background:linear-gradient(170deg,#c9d2dc,#8d98a3 50%,#5e6a55)"></div>
<div class="abs" style="left:480px;top:2850px;width:248px;height:30px;background:#fff"></div>
<div class="abs" style="left:488px;top:2856px;width:270px">
  <div class="news-date" style="font-size:10px">10.9.24</div>
  <div class="news-title" style="margin-top:16px;font-size:15px">Lorem ipsum dolor</div>
  <div class="news-text" style="margin-top:12px">Ut enim ad minim veniam quis nostrud exercitation ullamco laboris.</div>
  <div class="read" style="margin-top:8px">Read More...</div>
</div>

<div class="photo" role="img" aria-label="Electrician in hard hat examining wiring in a control room" style="left:789px;top:2685px;width:291px;height:190px;background:linear-gradient(110deg,#5a3b32,#a2452f 40%,#3d4450 75%,#c98a3c)"></div>
<div class="abs" style="left:789px;top:2850px;width:258px;height:30px;background:#fff"></div>
<div class="abs" style="left:797px;top:2856px;width:270px">
  <div class="news-date" style="font-size:10px">5.9.24</div>
  <div class="news-title" style="margin-top:16px;font-size:15px">Lorem ipsum dolor</div>
  <div class="news-text" style="margin-top:12px">Ut enim ad minim veniam quis nostrud exercitation ullamco laboris.</div>
  <div class="read" style="margin-top:8px">Read More...</div>
</div>

<!-- testimonials -->
<div class="abs" style="left:0;top:3056px;width:581px;height:444px;background:var(--blue)"></div>
<div class="photo" role="img" aria-label="Electrician on a ladder installing a ceiling light in a bright room" style="left:587px;top:3056px;width:613px;height:444px;background:linear-gradient(100deg,#dfe3e7,#b9c0c8 45%,#6a737d 65%,#e8ebee)"></div>
<div class="abs heading" style="left:108px;top:3083px;color:#fff"><span>Client <b style="color:#fff">Testimonials</b></span> <span class="dot-badge" style="border-color:#fff"></span></div>
<div class="photo" role="img" aria-label="Portrait of the client" style="left:109px;top:3170px;width:86px;height:86px;border-radius:50%;background:radial-gradient(circle,#d9b49a,#8a5a3e 75%);border:3px solid #fff"></div>
<div class="abs" style="left:229px;top:3176px;color:#fff;font-size:21px">Marisol Denvie</div>
<div class="abs" style="left:229px;top:3212px;color:var(--yellow);font-size:15px;letter-spacing:2px">★★★★★</div>
<div class="abs" style="left:410px;top:3192px;color:var(--yellow);font-size:54px;font-weight:900;line-height:1;font-family:Georgia,serif">”</div>
<div class="abs testi" style="left:117px;top:3270px">
  <p>Lorem ipsum dolor sit amet, consectetur adipiscing elit, sed do eiusmod tempor incididunt ut labore et dolore magna aliqua. Ut enim ad minim veniam, quis nostrud exercitation ullamco laboris nisi ut aliquip ex ea commodo consequat.</p>
</div>
<svg class="abs" style="left:125px;top:3442px" width="34" height="10"><circle cx="4" cy="5" r="3.5" fill="#fff"/><circle cx="15" cy="5" r="3.5" fill="#fff"/><circle cx="26" cy="5" r="3.5" fill="#fff"/></svg>
<svg class="abs" style="left:560px;top:3276px" width="50" height="50" viewBox="0 0 50 50"><circle cx="25" cy="25" r="22" fill="#fff"/><circle cx="25" cy="25" r="17" fill="var(--yellow)"/><path d="M21,18 L32,25 L21,32 Z" fill="#fff"/></svg>

<!-- contact -->
<div class="photo" role="img" aria-label="Model house with red roof beside a person holding a tablet" style="left:115px;top:3588px;width:385px;height:386px;background:linear-gradient(135deg,#4a4e53,#7d8086 45%,#e2ddd6 70%,#b7b2ab)"></div>
<div class="abs" style="left:741px;top:3616px;width:324px;height:310px;border:3px solid var(--yellow)"></div>
<div class="abs" style="left:436px;top:3633px;width:604px;height:414px;background:#fff;box-shadow:0 4px 18px rgba(0,0,0,.18)"></div>
<div class="abs heading" style="left:487px;top:3658px">Get&nbsp;&nbsp;In <b>Touch</b> <span class="dot-badge"></span></div>
<div class="abs field" style="left:487px;top:3728px;width:240px"><label>Your Name</label><span>Jhon Smith</span></div>
<div class="abs field" style="left:753px;top:3728px;width:240px"><label>Email</label><span>jhon.smith@mailbox.example</span></div>
<div class="abs field" style="left:487px;top:3814px;width:240px"><label>Company</label><span>Jsh Company</span></div>
<div class="abs field" style="left:753px;top:3814px;width:240px"><label>Phone</label><span>+1 (555) 014 2290</span></div>
<div class="abs field" style="left:487px;top:3904px;width:462px"><label>Message</label><span style="padding-bottom:30px">Hi , Do you have Moment To Talk About Us</span></div>
<svg class="abs" style="left:951px;top:3951px" width="48" height="48" viewBox="0 0 48 48"><circle cx="24" cy="24" r="23" fill="var(--blue)"/><path d="M14,24 L33,15 L27,34 L23,26 Z" fill="none" stroke="#fff" stroke-width="2" stroke-linejoin="round"/></svg>

<!-- footer -->
<svg class="abs" style="left:0;top:4100px" width="1200" height="463" viewBox="0 4100 1200 463">
  <path d="M0,4245 Q600,4040 1200,4245 L1200,4563 L0,4563 Z" fill="var(--yellow)"/>
  <path d="M0,4262 Q600,4062 1200,4262 L1200,4563 L0,4563 Z" fill="#050505"/>
  <circle cx="600" cy="4130" r="26" fill="#fff"/>
  <circle cx="600" cy="4130" r="21" fill="var(--yellow)"/>
</svg>
<div class="footer">
  <div class="brand" style="left:110px;top:4285px;color:#fff"><span class="l1" style="font-size:28px">FENNICK</span><span class="l2" style="font-size:28px">ELECTRIC</span></div>
  <div class="abs" style="left:112px;top:4374px;width:227px;height:36px;border-radius:18px;background:#fff;font-size:11px;color:#555;padding:12px 16px">Enter Email Address</div>
  <div class="pill" style="left:112px;top:4425px;width:116px;font-size:12px">Subscribe <i></i></div>

  <div class="abs" style="left:461px;top:4272px"><h4>Quick Links</h4>
    <ul class="flinks" style="margin-top:18px"><li>Home</li><li>About Us</li><li>Services</li><li>Projects</li><li>Careers</li><li>Testimonials</li><li>Blog</li></ul></div>

  <div class="abs" style="left:640px;top:4272px"><h4>Contact Info</h4>
    <ul class="contact" style="margin-top:22px">
      <li><svg width="20" height="20" viewBox="0 0 20 20"><circle cx="10" cy="10" r="10" fill="#fff"/><path d="M10,4 C7,4 6,6 6,8 C6,11 10,15 10,15 C10,15 14,11 14,8 C14,6 13,4 10,4 Z" fill="#050505"/></svg>Harlow Lane, CA - 95291</li>
      <li><svg width="20" height="20" viewBox="0 0 20 20"><circle cx="10" cy="10" r="10" fill="#fff"/><path d="M6,5 L8,5 L9,8 L8,9 C9,11 10,12 11,12 L12,11 L15,12 L15,14 C10,15 5,10 6,5 Z" fill="#050505"/></svg>+1 555 014 2290</li>
      <li><svg width="20" height="20" viewBox="0 0 20 20"><circle cx="10" cy="10" r="10" fill="#fff"/><rect x="5" y="6.5" width="10" height="7" fill="none" stroke="#050505" stroke-width="1.4"/><path d="M5,6.5 L10,10.5 L15,6.5" fill="none" stroke="#050505" stroke-width="1.4"/></svg>hello@fennickelectric.example</li>
    </ul></div>

  <div class="abs" style="left:941px;top:4272px"><h4>Follow Us</h4>
    <ul class="social" style="margin-top:18px"><li><i></i>Chatterpost</li><li><i></i>Quipline</li><li><i></i>Snapvale</li><li><i></i>Workreel</li></ul></div>

  <div class="abs" style="left:110px;top:4518px;width:975px;height:1px;background:#fff"></div>
  <div class="abs" style="left:0;top:4534px;width:1200px;text-align:center;font-size:12px;color:#fff">Copyright © 2024 Fennick Electric. All rights reserved.</div>
</div>

</div>
</body>
</html>
```